Catering Menu Package

I currently have a complete menu package, which we have redesigned as far as content, now I need to it put together in a catalog type format. It is essentially 10-12 pages in length, and will be sent for print production. Upon receiving a final edit
Updates

I have added an example gif to the project.

I did this free hand this basically what I am looking for. please change text and type to whatever you think would look best. This is a total rough design so, feel free to change any and everything. The text for the page is on the word documents. If you need more images let me know I am in the process of getting as many images uploaded for your use.

Project Deadline Extended
Reason: I figured we got a late jump with questions, so i am extending a few days .

Target Market(s)

The target market is business who wish to have catered luncheons, breakfasts , meetings

Industry/Entity Type

Catering

Requirements
Must have
• I have attached a copy of the text that what we want in the package, our logo, and i have also attached a catering package of another company to give you an idea what the finished product will be
Should not have
• It should not look identical to the example catering packages, these are for some inspiration we want our own design with the same type of look and feel

```html
<!DOCTYPE html>
<html lang="en">
<head>
<meta charset="utf-8">
<title>Harbor Hill Caterers – Breakfast Menu Pages</title>
<link href="https://fonts.googleapis.com/css2?family=Lobster+Two:ital,wght@1,700&family=Cormorant+Garamond:ital,wght@1,700&family=Libre+Baskerville:wght@700&family=Tinos&display=swap" rel="stylesheet">
<style>
  :root{
    --backdrop:#b5773f;
    --paper:#e9dfd2;
    --orange:#f07424;
    --orange-text:#ee7a2c;
    --ink:#1e1a17;
    --green:#5cb85a;
    --white:#ffffff;
  }
  *{margin:0;padding:0;box-sizing:border-box}
  html,body{width:1200px;height:800px;overflow:hidden}
  body{background:var(--backdrop);position:relative;font-family:'Tinos',serif}
  .page{position:absolute;top:18px;width:566px;height:744px;background:var(--paper);overflow:hidden}
  .page--front{left:22px}
  .page--back{left:607px;width:568px}
  .photo{position:absolute;top:0;left:0}
  .rule{position:absolute;height:5px;background:var(--orange)}
  .heading{position:absolute;background:var(--orange);color:var(--white);
    font-family:'Lobster Two',cursive;font-style:italic;font-weight:700;font-size:28px;
    line-height:40px;height:40px;padding:0 10px;white-space:nowrap;letter-spacing:.5px}
  .item{position:absolute;color:var(--orange-text);font-family:'Cormorant Garamond',serif;
    font-style:italic;font-weight:700;font-size:25px;line-height:24px}
  .item--center{text-align:center;width:440px;left:14px}
  .price{position:absolute;font-family:'Libre Baskerville',serif;font-weight:700;font-size:16px;color:var(--ink)}
  .price--center{width:440px;left:14px;text-align:center}
  .note{position:absolute;font-size:11px;color:var(--ink)}
  .notice{position:absolute;left:13px;top:654px;width:396px;height:29px;border-radius:8px;
    background:var(--green);color:var(--white);font-size:10px;line-height:12px;text-align:center;padding-top:3px}
  .footer{position:absolute;left:0;top:687px;width:420px;height:43px;background:var(--orange);color:var(--white)}
  .footer__cta{position:absolute;left:20px;top:3px;font-size:9px;font-style:italic}
  .footer__phone{position:absolute;left:32px;top:14px;font-family:'Libre Baskerville',serif;font-style:italic;font-size:20px;display:flex;align-items:center;gap:6px}
  .footer__address{position:absolute;left:238px;top:5px;font-size:10px;line-height:12.5px}
  .brand{position:absolute;left:415px;top:517px;width:153px;height:213px;background:var(--white);
    display:flex;flex-direction:column;align-items:center;justify-content:center;gap:14px}
  .brand__dot{width:46px;height:46px;border-radius:50%;background:var(--orange)}
  .brand__name{font-family:'Cormorant Garamond',serif;font-style:italic;font-weight:700;font-size:24px;
    line-height:26px;color:var(--ink);text-align:center}
</style>
</head>
<body>

<section class="page page--front">
  <svg class="photo" width="566" height="744" role="img" aria-label="Photo of a twice baked potato topped with melted cheese">
    <defs><linearGradient id="potato" x1="0" y1="0" x2="0" y2="1">
      <stop offset="0" stop-color="#9aa3a8"/><stop offset=".35" stop-color="#e7c66a"/>
      <stop offset=".7" stop-color="#8a7a62"/><stop offset="1" stop-color="#dfe3e6"/></linearGradient></defs>
    <path d="M470 0H566V517H415Q448 400 456 260Q462 110 470 0Z" fill="url(#potato)"/>
  </svg>

  <div class="rule" style="left:0;top:28px;width:440px"></div>
  <div class="heading" style="left:96px;top:10px">Breakfast Stratas</div>

  <div class="item item--center" style="top:68px">Breakfast Stratas-serves 10-12 ppl</div>
  <div class="price price--center" style="top:91px">$&amp;.&amp;&amp;</div>
  <div class="item item--center" style="top:123px">French Toast Strata</div>
  <div class="price price--center" style="top:147px">$&amp;.&amp;&amp;</div>
  <div class="item item--center" style="top:179px">Redskin Potato and Maple<br>Sausage Strata</div>
  <div class="price price--center" style="top:233px">$&amp;.&amp;&amp;</div>
  <div class="item item--center" style="top:266px">Twice Baked Breakfast<br>Potato Casserole</div>
  <div class="price price--center" style="top:319px">$&amp;.&amp;&amp;</div>

  <div class="rule" style="left:0;top:372px;width:458px"></div>
  <div class="heading" style="left:35px;top:354px">Ala Carte Breakfast Items</div>

  <div class="item" style="left:18px;top:414px">Buttermilk Pancakes</div>
  <div class="note" style="left:18px;top:440px">served with Warm Maple Syrup and Whipped Butter</div>
  <div class="price" style="left:328px;top:416px">$&amp;.&amp;&amp;</div>
  <div class="item" style="left:18px;top:470px">Redskin Potato Hash<br>Browns</div>
  <div class="price" style="left:328px;top:493px">$&amp;.&amp;&amp;</div>
  <div class="item" style="left:18px;top:533px">Maple Sausage Links</div>
  <div class="price" style="left:328px;top:537px">$&amp;.&amp;&amp;</div>
  <div class="item" style="left:18px;top:573px">Applewood Smoked Bacon</div>
  <div class="price" style="left:328px;top:578px">$&amp;.&amp;&amp;</div>
  <div class="item" style="left:15px;top:615px">Turkey Bacon</div>
  <div class="price" style="left:328px;top:620px">$&amp;.&amp;&amp;</div>

  <div class="notice">All Prices are per Person, with a 10 person minimum order per item chosen.<br>Local Products used when available and in season</div>
  <div class="footer">
    <div class="footer__cta">CALL OR EMAIL US TODAY:</div>
    <div class="footer__phone">
      <svg width="24" height="18" viewBox="0 0 24 18" aria-hidden="true"><path d="M2 6Q12-2 22 6L19 9 16 6V4H8V6L5 9Z" fill="#1e1a17"/><rect x="5" y="9" width="14" height="8" rx="2" fill="#1e1a17"/></svg>
      <span style="color:#1e1a17">555-014-2290</span>
    </div>
    <div class="footer__address">48 Birch Lane<br>Fairview, MD 20700<br>www.harborhillcaterers.com</div>
  </div>
  <div class="brand"><div class="brand__dot"></div><div class="brand__name">Harbor Hill<br>Caterers</div></div>
</section>

<section class="page page--back">
  <svg class="photo" width="568" height="744" role="img" aria-label="Photo of a glass of orange juice with sliced oranges">
    <defs><linearGradient id="juice" x1="0" y1="0" x2="1" y2="1">
      <stop offset="0" stop-color="#f4f4f2"/><stop offset=".4" stop-color="#f7b62c"/>
      <stop offset=".75" stop-color="#f08a16"/><stop offset="1" stop-color="#f6f2ea"/></linearGradient></defs>
    <path d="M450 0H568V517H420Q472 300 445 110Q444 40 450 0Z" fill="url(#juice)"/>
  </svg>

  <div class="item" style="left:31px;top:9px">Country Ham</div>
  <div class="price" style="left:354px;top:14px">$&amp;.&amp;&amp;</div>
  <div class="item" style="left:31px;top:47px">Fresh Fruit Platter</div>
  <div class="price" style="left:354px;top:50px">$&amp;.&amp;&amp;</div>
  <div class="item" style="left:27px;top:84px">Whole Fruit Basket</div>
  <div class="price" style="left:354px;top:86px">$&amp;.&amp;&amp;</div>

  <div class="rule" style="left:0;top:160px;width:470px"></div>
  <div class="heading" style="left:88px;top:142px">Breakfast Beverages</div>

  <div class="item" style="left:30px;top:216px">Fresh Squeezed Orange<br>Juice</div>
  <div class="price" style="left:326px;top:244px">$&amp;.&amp;&amp;</div>
  <div class="item" style="left:25px;top:296px">Cranberry Juice</div>
  <div class="price" style="left:326px;top:300px">$&amp;.&amp;&amp;</div>
  <div class="item" style="left:26px;top:343px">Apple Juice</div>
  <div class="price" style="left:326px;top:347px">$&amp;.&amp;&amp;</div>
  <div class="item" style="left:26px;top:389px">Bottled Water</div>
  <div class="price" style="left:326px;top:392px">$&amp;.&amp;&amp;</div>
  <div class="item" style="left:26px;top:436px">Bottled Juices</div>
  <div class="price" style="left:326px;top:440px">$&amp;.&amp;&amp;</div>
  <div class="item" style="left:25px;top:483px">Riverstone Select Gourmet<br>Coffee Station</div>
  <div class="price" style="left:326px;top:515px">$&amp;.&amp;&amp;</div>
  <div class="item" style="left:26px;top:564px">Hot Tea</div>
  <div class="price" style="left:326px;top:567px">$&amp;.&amp;&amp;</div>

  <div class="notice">All Prices are per Person, with a 10 person minimum order per item chosen.<br>Local Products used when available and in season</div>
  <div class="footer">
    <div class="footer__cta">CALL OR EMAIL US TODAY:</div>
    <div class="footer__phone">
      <svg width="24" height="18" viewBox="0 0 24 18" aria-hidden="true"><path d="M2 6Q12-2 22 6L19 9 16 6V4H8V6L5 9Z" fill="#1e1a17"/><rect x="5" y="9" width="14" height="8" rx="2" fill="#1e1a17"/></svg>
      <span style="color:#1e1a17">555-014-2290</span>
    </div>
    <div class="footer__address">48 Birch Lane<br>Fairview, MD 20700<br>www.harborhillcaterers.com</div>
  </div>
  <div class="brand"><div class="brand__dot"></div><div class="brand__name">Harbor Hill<br>Caterers</div></div>
</section>

</body>
</html>
```